Web Design For Staffing Company

We need a homepage web design for a technical staffing company.

Please see attached brief for project details.

please make the site modern with bold colors while matching the logo

Be sure to read the attached breif in full beforehand.

Target Market(s)

technical companies looking to hire talent

Industry/Entity Type

Staffing

Number of Pages Required

1 page

Font styles to use
Sans Serif

```html
<!DOCTYPE html>
<html lang="en">
<head>
<meta charset="utf-8">
<title>Halvern Recruiting – Home</title>
<link href="https://fonts.googleapis.com/css2?family=Roboto:wght@300;400;500;700;900&display=swap" rel="stylesheet">
<style>
:root{
  --blue:#1f6fc2;
  --blue-dark:#12569e;
  --blue-deep:#0d3f78;
  --ink:#222;
  --muted:#666;
  --light:#f4f6f9;
  --footer:#1d1f22;
  --footer-bar:#111214;
  --footer-text:#bbb;
  --white:#fff;
}
*{box-sizing:border-box;margin:0;padding:0}
html,body{width:1200px;height:3816px;overflow:hidden}
body{font-family:'Roboto',sans-serif;color:var(--ink);background:var(--white);position:relative}
.abs{position:absolute}
.btn{display:inline-flex;align-items:center;justify-content:center;gap:8px;height:40px;padding:0 26px;border-radius:20px;font-size:14px;font-weight:700;letter-spacing:.5px;text-transform:uppercase;white-space:nowrap}
.btn-blue{background:var(--blue);color:var(--white)}
.btn-white{background:var(--white);color:var(--blue)}
.btn-ghost{border:2px solid var(--white);color:var(--white)}

/* header */
.site-header{top:0;left:0;width:1200px;height:88px;background:var(--white);box-shadow:0 2px 6px rgba(0,0,0,.08)}
.brand{left:112px;top:30px;display:flex;align-items:center;gap:10px;font-size:22px;font-weight:700;color:var(--ink);white-space:nowrap}
.brand-square{width:12px;height:12px;background:var(--blue)}
.nav{left:372px;top:34px;display:flex;gap:26px;font-size:14px;font-weight:500}
.nav a{color:var(--ink);text-decoration:none}
.nav .active{color:var(--blue);border-bottom:2px solid var(--blue);padding-bottom:4px}
.search{left:792px;top:26px;width:172px;height:36px;border:1px solid #ccc;border-radius:18px;font-size:13px;color:#999;padding:9px 16px}
.search-btn{left:968px;top:26px;height:36px;padding:0 18px;font-size:13px}

/* hero */
.hero-photo{left:0;top:88px;width:1200px;height:564px;background:linear-gradient(120deg,#d9dee5,#aeb8c4 55%,#7d8894)}
.hero-panel{left:0;top:88px;width:470px;height:564px;background:linear-gradient(180deg,rgba(31,111,194,.85),rgba(13,63,120,.95))}
.hero-title{left:80px;top:270px;font-size:40px;font-weight:700;line-height:1.15;color:var(--white)}
.hero-sub{left:80px;top:384px;font-size:17px;color:var(--white)}
.hero-btns{left:80px;top:428px;display:flex;gap:20px}

/* intro */
.intro{left:210px;top:724px;width:780px;text-align:center;font-size:14px;line-height:1.7;color:var(--muted)}

/* feature rows */
.feature-photo{background:linear-gradient(135deg,#cfd6df,#9aa6b3)}
.card{background:var(--white);box-shadow:0 6px 24px rgba(0,0,0,.14);padding:36px 40px;font-size:14px;line-height:1.7;color:var(--muted)}
.card .btns{display:flex;gap:18px;justify-content:center;margin-top:26px}
.card.align-left .btns{justify-content:flex-start}

/* testimonial */
.testimonial{left:0;top:1932px;width:1200px;height:420px;background:linear-gradient(90deg,var(--blue-dark),var(--blue) 50%,var(--blue-dark))}
.testimonial h2{position:absolute;left:0;top:64px;width:1200px;text-align:center;color:var(--white);font-size:40px;font-weight:700;letter-spacing:1px}
.avatar{left:188px;top:2170px;width:64px;height:64px;border-radius:50%;background:#c9a98e}
.quote-text{left:284px;top:2164px;width:620px;color:var(--white);font-size:14px;line-height:1.6;font-style:italic}
.quote-name{left:284px;top:2256px;color:var(--white);font-size:14px;font-weight:700}
.quote-role{left:284px;top:2278px;color:#d2e2f4;font-size:12px}
.arrow{top:2180px}
.quote-mark{font-size:90px;color:rgba(255,255,255,.25);font-family:Georgia,serif;line-height:1}

/* blog */
.section-title{left:0;width:1200px;text-align:center;font-size:40px;font-weight:700;color:var(--ink)}
.post{top:2528px;width:308px;height:432px;background:var(--light)}
.post-img{width:308px;height:224px;background:linear-gradient(135deg,#b9c1cb,#7e8894)}
.post-meta{display:flex;gap:14px;padding:14px 16px 6px;font-size:11px;color:var(--muted)}
.post-meta span::before{content:"";display:inline-block;width:8px;height:8px;background:var(--blue);margin-right:6px}
.post h3{padding:4px 16px;font-size:19px;font-weight:700;line-height:1.25}
.post p{padding:6px 16px;font-size:12px;line-height:1.5;color:var(--muted)}
.post .btn{margin:6px 16px;height:30px;padding:0 16px;font-size:11px}

/* contact */
.contact-box{top:3120px;width:352px;height:220px;background:linear-gradient(135deg,var(--blue),var(--blue-deep));color:var(--white);text-align:center;padding-top:48px}
.contact-box h3{font-size:21px;font-weight:700;line-height:1.3;text-transform:uppercase}
.contact-box .btn{margin-top:22px;height:36px}

/* footer */
.footer{left:0;top:3448px;width:1200px;height:300px;background:var(--footer)}
.foot-col{top:3488px;width:300px;color:var(--footer-text)}
.foot-col h4{color:var(--white);font-size:15px;font-weight:700;margin-bottom:16px;text-transform:uppercase}
.foot-col p{font-size:13px;line-height:1.6;color:var(--footer-text);height:42px}
.foot-col .btn{margin-top:20px;height:36px}
.foot-bar{left:0;top:3748px;width:1200px;height:68px;background:var(--footer-bar);color:#aaa;font-size:13px;text-align:center;line-height:68px}
.chat{left:1128px;top:3700px;width:40px;height:40px;border-radius:50%;background:var(--blue)}
</style>
</head>
<body>

<header class="site-header abs">
  <div class="brand abs"><span class="brand-square"></span>Halvern</div>
  <nav class="nav abs">
    <a class="active">HOME</a><a>ABOUT</a><a>JOB SEEKERS</a><a>CLIENTS</a><a>CONTACT</a>
  </nav>
  <div class="search abs">Search Jobs</div>
  <div class="search-btn btn btn-blue abs">Search Jobs</div>
</header>

<div class="hero-photo abs" role="img" aria-label="Photo of a team of professionals collaborating around laptops in an office"></div>
<div class="hero-panel abs"></div>
<h1 class="hero-title abs">The Right People For<br>The Right Jobs!</h1>
<p class="hero-sub abs">Bridging the talent gap in Technical Staffing</p>
<div class="hero-btns abs">
  <span class="btn btn-white">Hire Talent</span>
  <span class="btn btn-ghost">Get Hired</span>
</div>

<p class="intro abs">Halvern Recruiting is a National Technical Staffing and Recruiting Solutions Provider founded in 2013 focused on matching contract and full-time Engineering and IT professionals with new and exciting employment opportunities!</p>

<div class="feature-photo abs" style="left:112px;top:840px;width:488px;height:420px" role="img" aria-label="Photo of a smiling professional woman at a laptop"></div>
<div class="card abs" style="left:540px;top:900px;width:540px;height:340px">
  <p>Simply said... WE LOVE TO RECRUIT! It's our passion and we take it very seriously! It is not easy for JOB SEEKERS to put their job search efforts and trust in the hands of someone else, especially when there are so many Staffing Firms to choose from. So how do you know you are choosing the best Staffing Representation possible?</p>
  <div class="btns">
    <span class="btn btn-blue">Learn More &#9656;</span>
    <span class="btn btn-blue">View Jobs &#9656;</span>
  </div>
</div>

<div class="feature-photo abs" style="left:600px;top:1428px;width:488px;height:412px" role="img" aria-label="Photo of business people talking in a modern office"></div>
<div class="card align-left abs" style="left:112px;top:1500px;width:548px;height:340px">
  <p>Are you responsible for Technical Staffing within your organization? Are you satisfied with your current Supplier(s)' overall performance? Does it appear they identify potential Candidates based purely on "buzz word" searches? Is it evident they just do not grasp the scope and responsibilities of your technical staffing need(s)?</p>
  <div class="btns">
    <span class="btn btn-blue">Learn More &#9656;</span>
    <span class="btn btn-blue">Hire Talent &#9656;</span>
  </div>
</div>

<section class="testimonial abs"><h2>TESTIMONIAL</h2></section>
<svg class="arrow abs" style="left:100px" width="24" height="40" viewBox="0 0 24 40"><path d="M18 4 4 20l14 16" fill="none" stroke="#fff" stroke-width="4"/></svg>
<svg class="arrow abs" style="left:1076px" width="24" height="40" viewBox="0 0 24 40"><path d="M6 4l14 16L6 36" fill="none" stroke="#fff" stroke-width="4"/></svg>
<div class="quote-mark abs" style="left:262px;top:2130px">&ldquo;</div>
<div class="quote-mark abs" style="left:900px;top:2200px">&rdquo;</div>
<div class="avatar abs" role="img" aria-label="Portrait of the reviewer"></div>
<p class="quote-text abs">Sam's team is an excellent recruiter. He is articulate, honest, has a great manner and is an effective communicator between the clients and candidates. His goal is to find the right fit for the long term and he truly builds relationships that last.</p>
<p class="quote-name abs">Sam R</p>
<p class="quote-role abs">Electrical Test Engineer in the automotive sector</p>

<h2 class="section-title abs" style="top:2454px">OUR BLOG</h2>
<article class="post abs" style="left:112px">
  <div class="post-img" role="img" aria-label="Black and white photo of a historic thinker with a quote"></div>
  <div class="post-meta"><span>June 13, 2019</span><span>Industry</span></div>
  <h3>Tips for Spotting a U.S. Recession Before it Becomes Official</h3>
  <p>As the U.S. nears a record-long expansion, here is how to read the signs.</p>
  <span class="btn btn-blue">Read More</span>
</article>
<article class="post abs" style="left:444px">
  <div class="post-img" role="img" aria-label="Photo of a person working on a laptop"></div>
  <div class="post-meta"><span>June 11, 2019</span><span>Job Seekers</span></div>
  <h3>Ways To Make The Most Of The Hot Job Market</h3>
  <p>This is the tightest labor market in years, and candidates now have leverage.</p>
  <span class="btn btn-blue">Read More</span>
</article>
<article class="post abs" style="left:776px">
  <div class="post-img" role="img" aria-label="Photo of a manager meeting with employees"></div>
  <div class="post-meta"><span>June 4, 2019</span><span>Clients</span></div>
  <h3>Meeting Employees' Needs To Improve Performance</h3>
  <p>The benefits of keeping employees satisfied are well established, so act now.</p>
  <span class="btn btn-blue">Read More</span>
</article>

<h2 class="section-title abs" style="top:3036px">CONTACT US</h2>
<div class="contact-box abs" style="left:228px">
  <h3>Looking for Career - Minded<br>Candidates?</h3>
  <span class="btn btn-ghost">Request Talent</span>
</div>
<div class="contact-box abs" style="left:620px">
  <h3>Looking for Career -<br>Opportunities?</h3>
  <span class="btn btn-ghost">Search Jobs</span>
</div>

<footer class="footer abs"></footer>
<div class="foot-col abs" style="left:112px">
  <h4>Get Hired</h4>
  <p>Search our extensive list of available jobs to find your ideal match.</p>
  <span class="btn btn-blue">&#9906; Search Now</span>
</div>
<div class="foot-col abs" style="left:452px">
  <h4>Request an Employee</h4>
  <p>We're here to provide the people you need to get work done.</p>
  <span class="btn btn-blue">&#9654; Start Today</span>
</div>
<div class="foot-col abs" style="left:792px">
  <h4>Address</h4>
  <p>Halvern Recruiting Inc, 48 Harbor Lane, Suite 2, Millbrook, MA 01999</p>
  <span class="btn btn-blue">&#9993; Contact Us</span>
</div>
<div class="chat abs"></div>
<div class="foot-bar abs">&copy; 2020 · Technical Staffing Company · All Rights Reserved</div>

</body>
</html>
```